Unique Business Card Design

Unique Business Card design for our orthotic and prosthetic company. Our logo is on our website, color is light blue. Unique shape (artificial leg shaped, vertical, etc..) preferred. Logo, business name, individual name and basic demographics needed.

Industry/Entity Type

Business

Contact Information for Business Card

Logo, Industry, Phone # Logo, "Prosthetic & Orthotic Services" Place to add individual name and contact info

Colors
cee9f5

Requirements
Must have
• The icon must be there, placement of "Prosthetic & Orthotic Services" can be moved
Nice to have
• Like the mix of light blue, and a little darker blue. One design included the icons from my website which was a nice touch

```html
<!DOCTYPE html>
<html lang="en">
<head>
<meta charset="utf-8">
<title>Limbworks Inc. — Business Card</title>
<link rel="stylesheet" href="https://fonts.googleapis.com/css2?family=Open+Sans:wght@400;600;700&family=Cormorant+Garamond:ital,wght@1,500&display=swap">
<style>
  :root {
    --brand-blue: #1658a8;
    --brand-blue-deep: #0f4a93;
    --paper: #ffffff;
    --backdrop: #e8ebee;
    --light-blue: #cee9f5;
  }
  * { box-sizing: border-box; margin: 0; padding: 0; }
  html, body { width: 1200px; height: 900px; overflow: hidden; }
  body {
    background: var(--backdrop);
    font-family: "Open Sans", Arial, sans-serif;
    position: relative;
  }
  .card {
    position: absolute;
    left: 250px;
    width: 700px;
    height: 400px;
    box-shadow: 0 6px 18px rgba(0,0,0,0.12);
    overflow: hidden;
  }
  .card--front { top: 30px; background: linear-gradient(135deg, var(--brand-blue), var(--brand-blue-deep)); color: var(--paper); }
  .card--back { top: 470px; background: var(--paper); color: var(--brand-blue); }

  .badge {
    position: absolute;
    border-radius: 50%;
  }
  .card--front .badge { left: 90px; top: 140px; width: 120px; height: 120px; background: var(--paper); }

  .brand { position: absolute; }
  .card--front .brand { left: 245px; top: 152px; }
  .brand__name {
    font-weight: 600;
    letter-spacing: 1px;
    text-transform: uppercase;
    line-height: 1;
  }
  .card--front .brand__name { font-size: 40px; }
  .brand__rule { height: 2px; background: currentColor; margin: 8px 0 6px; }
  .brand__tagline {
    font-family: "Cormorant Garamond", Georgia, serif;
    font-style: italic;
    font-weight: 500;
  }
  .card--front .brand__tagline { font-size: 24px; padding-left: 30px; }

  /* back */
  .card--back .badge { left: 40px; top: 42px; width: 72px; height: 72px; background: var(--brand-blue); }
  .card--back .brand { left: 130px; top: 48px; }
  .card--back .brand__name { font-size: 28px; }
  .card--back .brand__rule { margin: 6px 0 4px; height: 1.5px; }
  .card--back .brand__tagline { font-size: 17px; padding-left: 18px; }

  .holder { position: absolute; left: 44px; top: 142px; font-size: 24px; }
  .holder__first { font-weight: 700; }
  .holder__creds { font-size: 17px; }

  .contact-list { position: absolute; left: 48px; top: 188px; list-style: none; }
  .contact-list li {
    display: flex; align-items: center; gap: 12px;
    font-size: 17px; line-height: 30px; color: var(--brand-blue);
  }
  .contact-list svg { width: 18px; height: 18px; flex: none; }

  .figure-area {
    position: absolute; right: 0; top: 0;
    width: 230px; height: 400px;
    background: linear-gradient(180deg, var(--brand-blue), var(--brand-blue-deep));
  }
</style>
</head>
<body>

<section class="card card--front">
  <div class="badge" aria-hidden="true"></div>
  <div class="brand">
    <div class="brand__name">Limbworks Inc.</div>
    <div class="brand__rule"></div>
    <div class="brand__tagline">Prosthetic &amp; Orthotic Services</div>
  </div>
</section>

<section class="card card--back">
  <div class="badge" aria-hidden="true"></div>
  <div class="brand">
    <div class="brand__name">Limbworks Inc.</div>
    <div class="brand__rule"></div>
    <div class="brand__tagline">Prosthetic &amp; Orthotic Services</div>
  </div>

  <div class="holder"><span class="holder__first">Miriam</span> Halvorsen, <span class="holder__creds">CO LPO</span></div>

  <ul class="contact-list">
    <li>
      <svg viewBox="0 0 20 20"><circle cx="10" cy="10" r="10" fill="var(--brand-blue)"/><path d="M6.5 5.5l2 0 .8 2.4-1.3 1a6 6 0 0 0 2.9 2.9l1-1.3 2.4.8v2a1 1 0 0 1-1 1A8.5 8.5 0 0 1 5.5 6.5a1 1 0 0 1 1-1z" fill="#fff"/></svg>
      555.210.4400
    </li>
    <li>
      <svg viewBox="0 0 20 20"><circle cx="10" cy="10" r="10" fill="var(--brand-blue)"/><rect x="5" y="8" width="10" height="6" rx="1" fill="#fff"/><rect x="7" y="5" width="6" height="3" fill="#fff"/></svg>
      555.210.4419
    </li>
    <li>
      <svg viewBox="0 0 20 20"><circle cx="10" cy="10" r="10" fill="var(--brand-blue)"/><rect x="7" y="4.5" width="6" height="11" rx="1" fill="#fff"/><rect x="8" y="6" width="4" height="6.5" fill="var(--brand-blue)"/></svg>
      555-348.2271
    </li>
    <li>
      <svg viewBox="0 0 20 20"><circle cx="10" cy="10" r="10" fill="var(--brand-blue)"/><rect x="5" y="6.5" width="10" height="7" rx="1" fill="#fff"/><path d="M5.5 7l4.5 3.5L14.5 7" stroke="var(--brand-blue)" stroke-width="1.2" fill="none"/></svg>
      mhalvorsen@limbworksinc.com
    </li>
    <li>
      <svg viewBox="0 0 20 20"><circle cx="10" cy="10" r="10" fill="var(--brand-blue)"/><circle cx="10" cy="10" r="4.5" stroke="#fff" stroke-width="1.3" fill="none"/><path d="M5.5 10h9M10 5.5v9" stroke="#fff" stroke-width="1.1"/></svg>
      www.limbworksinc.com
    </li>
    <li>
      <svg viewBox="0 0 20 20"><circle cx="10" cy="10" r="10" fill="var(--brand-blue)"/><path d="M10 4.5a3.5 3.5 0 0 1 3.5 3.5c0 2.6-3.5 7-3.5 7s-3.5-4.4-3.5-7A3.5 3.5 0 0 1 10 4.5z" fill="#fff"/><circle cx="10" cy="8" r="1.3" fill="var(--brand-blue)"/></svg>
      820 Alder Row, Millbrook, NY 10990
    </li>
  </ul>

  <div class="figure-area" role="img" aria-label="Large blue silhouette of a standing person with a prosthetic leg"></div>
</section>

</body>
</html>
```